Yard sign

Looking for a yard sign. <br/>Something simple, name, number. <br/>Large text, readable from 50 feet away. <br/><br/>18 x 24 inches.

Target Market(s)

Potential homeowners thinking about going solar.

Colors

Designer to choose colors to be used in the design.

Requirements
Must have
• "WE'VE GONE SOLAR!"
Nice to have
• We are a solar company, we would like a design that compliments the homeowners decision that they went solar and encourages others to do the same.

```html
<!DOCTYPE html>
<html lang="en">
<head>
<meta charset="UTF-8">
<title>We've Gone Solar – Yard Sign</title>
<link href="https://fonts.googleapis.com/css2?family=Bebas+Neue&family=Montserrat:wght@700;800&display=swap" rel="stylesheet">
<style>
  :root {
    --backdrop: #231f20;
    --panel-light: #4b4a4a;
    --panel-dark: #1d1c1c;
    --sun-yellow: #fbb515;
    --solar-orange: #f07a10;
    --deep-orange: #e35205;
    --accent-line: #f55a0a;
    --ink: #0a0a0a;
    --paper: #ffffff;
  }
  html, body {
    margin: 0;
    padding: 0;
    width: 1200px;
    height: 1200px;
    overflow: hidden;
    background: var(--backdrop);
  }
  .canvas {
    position: relative;
    width: 1200px;
    height: 1200px;
  }
  .yard-sign {
    position: absolute;
    left: 45px;
    top: 184px;
    width: 1110px;
    height: 832px;
  }
  .yard-sign svg { display: block; }
  .headline {
    font-family: "Bebas Neue", "Oswald", sans-serif;
    font-size: 172px;
  }
  .brand-name {
    font-family: "Montserrat", sans-serif;
    font-weight: 800;
    font-size: 78px;
    fill: var(--solar-orange);
  }
  .phone-number {
    font-family: "Montserrat", sans-serif;
    font-weight: 800;
    font-size: 132px;
    fill: var(--deep-orange);
  }
  .rep-name {
    font-family: "Montserrat", sans-serif;
    font-weight: 700;
    font-size: 52px;
    fill: var(--ink);
  }
</style>
</head>
<body>
<div class="canvas">
  <div class="yard-sign">
    <svg width="1110" height="832" viewBox="0 0 1110 832" xmlns="http://www.w3.org/2000/svg">
      <defs>
        <radialGradient id="panelShade" cx="50%" cy="35%" r="70%">
          <stop offset="0" stop-color="var(--panel-light)"/>
          <stop offset="1" stop-color="var(--panel-dark)"/>
        </radialGradient>
        <linearGradient id="headlineFill" x1="0" y1="0" x2="0" y2="1">
          <stop offset="0" stop-color="#fbb515"/>
          <stop offset="1" stop-color="#e35205"/>
        </linearGradient>
      </defs>

      <rect class="sign-dark-field" x="0" y="0" width="1110" height="832" fill="url(#panelShade)"/>
      <path class="sign-white-field" d="M0,474 Q555,718 1110,474 L1110,832 L0,832 Z" fill="var(--paper)"/>
      <path class="sign-divider-curve" d="M0,474 Q555,718 1110,474" fill="none" stroke="var(--accent-line)" stroke-width="9"/>

      <text class="headline" x="79" y="176" textLength="950" lengthAdjust="spacingAndGlyphs" fill="url(#headlineFill)">WE'VE GONE SOLAR!</text>

      <g class="brand-lockup">
        <circle cx="345" cy="380" r="90" fill="var(--sun-yellow)"/>
        <text class="brand-name" x="460" y="372" textLength="380" lengthAdjust="spacingAndGlyphs">SUNVALE</text>
        <text class="brand-name" x="460" y="452" textLength="262" lengthAdjust="spacingAndGlyphs">SOLAR</text>
      </g>

      <text class="phone-number" x="139" y="723" textLength="831" lengthAdjust="spacingAndGlyphs">555 210 4863</text>

      <g class="rep-line">
        <polygon points="147,764 330,761 330,767 147,766" fill="var(--ink)"/>
        <polygon points="780,761 964,764 964,766 780,767" fill="var(--ink)"/>
        <text class="rep-name" x="352" y="788" textLength="406" lengthAdjust="spacingAndGlyphs">MARCUS HALE</text>
      </g>
    </svg>
  </div>
</div>
</body>
</html>
```